BrivoTerna. Lantern of the Steady Harvest. Business card

Professional business card for BrivoTerna (Lantern of the Steady Harvest)
My rationale: Strategy-> Execution-> Results-> Value that lead to the BrivoTerna name: We put the Lantern of the Steady Harvest.
We deliver value to our customers helping them at defining a good strategy (cyan arrow). 90% of well formulated strategies fail due to poor execution so we also consider strategical execution very important (green arrow). Due to the execution we obtain the results (blue arrow). Finally, the results provide feedback to redefine strategy, and the new strategy has to be executed and new results obtained providing new feedback and on and on. It's like a wheel that finally, must create corporate value: value for shareholders, staholders, employees, providers...-

Target Market(s)

CEOs and steering comitees , invewrnent funds

Industry/Entity Type

Business Consultant

Contact Information for Business Card

Teodoro Vinsquel
CEO & Founder
teodoro.vinsquel@brivoterna-example.com
Mobile: +34 655.803.912
www.brivoterna-example.com

Colors

Designer to choose colors to be used in the design.

Requirements
Nice to have
• Nice to hace the words: Strategy, execution, results
• Nice to vave the claim: Lantern of the Steady Harvest
• The three colors should be shown:
• cyan for STRATEGY
• green for EXECUTION
• blue for RESULTS
Should not have
• Complete black background

```html
<!DOCTYPE html>
<html lang="en">
<head>
<meta charset="utf-8">
<title>BrivoTerna — Business Card</title>
<link rel="stylesheet" href="https://fonts.googleapis.com/css2?family=Open+Sans:wght@400;600;700;800&display=swap">
<style>
  :root {
    --card-blue: #0a2f9e;
    --card-white: #ffffff;
    --accent-green: #8cc63f;
    --accent-cyan: #29abe2;
    --page-bg: #e9ebf0;
    --text-light: #ffffff;
  }
  * { margin: 0; padding: 0; box-sizing: border-box; }
  html, body {
    width: 1200px; height: 900px; overflow: hidden;
    background: var(--page-bg);
    font-family: "Open Sans", Arial, sans-serif;
  }
  .canvas { position: relative; width: 1200px; height: 900px; }
  .card {
    position: absolute; width: 620px; height: 354px;
    border-radius: 22px; overflow: hidden;
    background: var(--card-blue);
    box-shadow: 0 10px 30px rgba(10, 30, 90, 0.18);
  }
  .card-front { left: 90px; top: 90px; }
  .card-back { left: 490px; top: 456px; }
  .front-curve { position: absolute; inset: 0; width: 100%; height: 100%; }
  .contact {
    position: absolute; left: 34px; top: 82px; color: var(--text-light);
  }
  .contact-name { font-size: 21px; font-weight: 700; line-height: 1.2; }
  .contact-role { font-size: 16px; font-weight: 400; margin-bottom: 12px; }
  .contact-line {
    display: flex; align-items: center; gap: 8px;
    font-size: 12px; line-height: 1.6; white-space: nowrap;
  }
  .contact-line svg { width: 12px; height: 12px; flex: none; }
  .website {
    position: absolute; left: 34px; bottom: 30px;
    color: var(--text-light); font-size: 14px; letter-spacing: 2.5px;
  }
  .website b { font-weight: 700; }
  .brand-name {
    position: absolute; font-weight: 800; letter-spacing: -0.5px; white-space: nowrap;
  }
  .card-front .brand-name {
    right: 30px; top: 150px; font-size: 36px; color: var(--card-blue);
  }
  .card-back .brand-name {
    left: 0; right: 0; top: 144px; text-align: center;
    font-size: 56px; color: var(--card-white);
  }
</style>
</head>
<body>
<main class="canvas">
  <section class="card card-front" aria-label="Business card front">
    <svg class="front-curve" viewBox="0 0 620 354" aria-hidden="true">
      <path d="M360 0 C320 140 360 300 460 354 L620 354 L620 0 Z" fill="var(--card-white)"/>
      <path d="M368 0 C328 140 368 300 472 354 L620 354 L620 0 Z" fill="var(--accent-green)"/>
      <path d="M376 0 C336 140 376 300 484 354 L620 354 L620 0 Z" fill="var(--accent-cyan)"/>
      <path d="M382 0 C342 140 382 300 494 354 L620 354 L620 0 Z" fill="var(--card-white)"/>
    </svg>
    <div class="contact">
      <p class="contact-name">Teodoro Vinsquel</p>
      <p class="contact-role">CEO &amp; Founder</p>
      <p class="contact-line">
        <svg viewBox="0 0 24 24" aria-hidden="true"><path fill="#fff" d="M6.6 10.8a15.1 15.1 0 0 0 6.6 6.6l2.2-2.2a1 1 0 0 1 1-.25 11.4 11.4 0 0 0 3.6.57 1 1 0 0 1 1 1V20a1 1 0 0 1-1 1A17 17 0 0 1 3 4a1 1 0 0 1 1-1h3.5a1 1 0 0 1 1 1c0 1.25.2 2.45.57 3.57a1 1 0 0 1-.25 1z"/></svg>
        +34 655.803.912
      </p>
      <p class="contact-line">
        <svg viewBox="0 0 24 24" aria-hidden="true"><path fill="#fff" d="M3 5h18v14H3z M4.5 6.5v.6l7.5 5 7.5-5v-.6z" fill-rule="evenodd"/></svg>
        teodoro.vinsquel@brivoterna-example.com
      </p>
    </div>
    <p class="website">www.<b>brivoterna-example</b>.com</p>
    <p class="brand-name">BrivoTerna</p>
  </section>

  <section class="card card-back" aria-label="Business card back">
    <p class="brand-name">BrivoTerna</p>
  </section>
</main>
</body>
</html>
```